Business Card Design Project

We need a Business Card for an Mechanical Engineering firm in Singapore. The design should be Modern & Technical looking, yet eye catching.

Our company deals in Cutting Tools & Machine Accessories for the Manufacturing Industries such as Oil & Gas, Aero Space, etc... For more information on our Company, you can either email me or view our website www.torvalen.com.sg.

We are trying to revamp our image to give our consumers a fresh new perspective to our company, so we welcome all ideas.

Industry/Entity Type

Business

Requirements
Must have
• Must incorporate New Company Logo into the card as shown in Uploaded file.

```html
<!DOCTYPE html>
<html lang="en">
<head>
<meta charset="utf-8">
<title>Torvalen Tools – Business Card</title>
<link rel="stylesheet" href="https://fonts.googleapis.com/css2?family=Open+Sans:ital,wght@0,400;0,600;1,400&display=swap">
<style>
  :root {
    --stage: #e4e4e4;
    --card-dark: #1a1616;
    --card-light: #ffffff;
    --brand-red: #8e1b22;
    --ink: #2b2b2b;
    --ink-soft: #555555;
    --white: #ffffff;
    --swoosh-dark: #141212;
  }
  * { box-sizing: border-box; margin: 0; padding: 0; }
  html, body { width: 1200px; height: 951px; overflow: hidden; }
  body {
    background: var(--stage);
    font-family: "Open Sans", Arial, sans-serif;
    position: relative;
  }
  .card {
    position: absolute;
    left: 250px;
    width: 700px;
    height: 400px;
    border-radius: 26px;
    overflow: hidden;
    box-shadow: 0 6px 18px rgba(0,0,0,0.18);
  }
  .card--front { top: 50px; background: var(--card-dark); }
  .card--back  { top: 500px; background: var(--card-light); }

  /* Front */
  .front-brand {
    position: absolute;
    top: 120px; left: 0; right: 0;
    display: flex; align-items: center; justify-content: center; gap: 18px;
  }
  .brand-dot {
    width: 30px; height: 30px; border-radius: 50%;
    background: var(--brand-red);
  }
  .brand-name {
    font-weight: 600;
    font-size: 52px;
    letter-spacing: 1px;
    text-transform: uppercase;
    line-height: 1;
  }
  .front-brand .brand-name { color: var(--white); }
  .front-web {
    position: absolute;
    top: 268px; left: 0; right: 0;
    text-align: center;
    color: var(--white);
    font-size: 21px;
    letter-spacing: 0.5px;
  }

  /* Back */
  .back-brand {
    position: absolute;
    top: 70px; left: 58px;
    display: flex; align-items: center; gap: 12px;
  }
  .back-brand .brand-name { color: var(--brand-red); font-size: 36px; }
  .back-brand .brand-dot { width: 22px; height: 22px; }

  .holder {
    position: absolute;
    top: 66px; left: 470px;
  }
  .holder-name { font-size: 23px; color: var(--ink); }
  .holder-role { font-size: 18px; font-style: italic; color: var(--brand-red); }

  .address {
    position: absolute;
    top: 178px; left: 58px;
    display: flex; gap: 10px;
    font-size: 20px; line-height: 1.4; color: var(--ink);
  }
  .contacts {
    position: absolute;
    top: 176px; left: 360px;
    list-style: none;
    font-size: 19px; line-height: 1.42; color: var(--ink);
  }
  .contacts li { display: flex; align-items: center; gap: 10px; }
  .icon { width: 16px; height: 16px; flex: none; fill: var(--brand-red); }
  .address .icon { margin-top: 5px; }
  .web-accent { color: var(--brand-red); }

  .swoosh { position: absolute; left: 0; bottom: 0; width: 700px; height: 150px; }
</style>
</head>
<body>

<section class="card card--front" aria-label="Card front">
  <div class="front-brand">
    <span class="brand-dot"></span>
    <span class="brand-name">Torvalen Tools</span>
  </div>
  <p class="front-web">www.torvalentools.com</p>
</section>

<section class="card card--back" aria-label="Card back">
  <div class="back-brand">
    <span class="brand-dot"></span>
    <span class="brand-name">Torvalen Tools</span>
  </div>

  <div class="holder">
    <p class="holder-name">Marcus Lindqvar</p>
    <p class="holder-role">manager</p>
  </div>

  <div class="address">
    <svg class="icon" viewBox="0 0 16 16" aria-hidden="true"><path d="M8 1 0 8h2v7h4v-4h4v4h4V8h2z"/></svg>
    <p>1480 Kestrel Row<br>Delmont, TX 78114</p>
  </div>

  <ul class="contacts">
    <li><svg class="icon" viewBox="0 0 16 16" aria-hidden="true"><path d="M3 1h3l1 4-2 1c1 2 2 3 4 4l1-2 4 1v3c0 1-1 2-2 2C6 14 2 10 1 3c0-1 1-2 2-2z"/></svg>512-004-2710</li>
    <li><svg class="icon" viewBox="0 0 16 16" aria-hidden="true"><rect x="4" y="1" width="8" height="14" rx="1.5"/></svg>512-004-2711</li>
    <li><svg class="icon" viewBox="0 0 16 16" aria-hidden="true"><path d="M1 4h14v9H1z M1 4l7 5 7-5" /></svg>info@torvalentools.com</li>
    <li><svg class="icon" viewBox="0 0 16 16" aria-hidden="true"><circle cx="8" cy="8" r="7"/></svg><span>www.<span class="web-accent">torvalentools</span>.com</span></li>
  </ul>

  <svg class="swoosh" viewBox="0 0 700 150" preserveAspectRatio="none" aria-hidden="true">
    <path d="M0 20 C120 40 250 110 700 120 L700 150 L0 150 Z" fill="var(--swoosh-dark)"/>
    <path d="M0 70 C180 95 300 125 700 95 L700 150 L0 150 Z" fill="var(--brand-red)"/>
    <path d="M0 115 C200 135 420 140 700 128 L700 150 L0 150 Z" fill="var(--card-light)" opacity="0.15"/>
  </svg>
</section>

</body>
</html>
```